Flat bootstrap design for existing site

I'm looking for a modern flat design based around an existing logo. This has to be a custom design (no external templates), and implemented into a bootstrap framework.

The logo is attached as 2 versions - choose whichever you want, that flows better with whatever design you choose.

Added screenshots of the existing site (currently using the default bootstrap layouts). Please make your designs around those pages in the screenshots (i.e. the homepage only has the postal code input and the header). The active page has 3 screenshots, because I wanted to illustrate the other states that would be visible (in the table rows).

This is a moving/junk removal website, just for some context.

Here's some example websites (flat designs) that I like, just to give you an idea of what I'm after.

https://www.plimvora.com/
https://dacklow.com/
https://trevanu.com/
https://quobrintal.com/en/

Coding

Coded - Design and coding required

Number of Pages Required

5+ page

Colors

Designer to choose colors to be used in the design.

Requirements
Must have
• It must be a modern/simple flat design, that is built around the existing logo (attached).
• It has to be implemented using bootstrap.

```html
<!DOCTYPE html>
<html lang="en">
<head>
<meta charset="utf-8">
<title>Haulvek – Booking Details</title>
<link href="https://fonts.googleapis.com/css2?family=Lato:wght@400;700&family=Open+Sans:wght@400;600&display=swap" rel="stylesheet">
<style>
  :root {
    --header-a: #63c9ec;
    --header-b: #7dd6f3;
    --accent: #45c5f0;
    --table-head: #229bc8;
    --ink: #333a3f;
    --muted: #555c61;
    --line: #c9cdd0;
    --field-line: #b9bec2;
    --ok: #6aaa5a;
    --sent: #74c1dd;
    --pending: #777777;
    --white: #ffffff;
  }
  * { box-sizing: border-box; margin: 0; padding: 0; }
  html, body { width: 1130px; height: 1200px; overflow: hidden; background: var(--white); }
  body { font-family: "Open Sans", Arial, sans-serif; color: var(--ink); position: relative; }

  .site-header {
    position: absolute; left: 0; top: 0; width: 1130px; height: 99px;
    background: linear-gradient(120deg, var(--header-a), var(--header-b) 55%, var(--header-a));
  }
  .brand {
    position: absolute; left: 93px; top: 30px;
    font-family: "Lato", Arial, sans-serif; font-weight: 700; font-size: 34px;
    color: var(--white); letter-spacing: 1px; display: flex; align-items: center; gap: 10px;
  }
  .brand-dot { width: 14px; height: 14px; border-radius: 50%; background: var(--white); }
  .main-nav {
    position: absolute; top: 40px; left: 520px;
    display: flex; gap: 36px; font-family: "Lato", Arial, sans-serif; font-size: 15px;
    color: var(--white); text-transform: uppercase;
  }
  .main-nav a { color: inherit; text-decoration: none; padding-bottom: 5px; }
  .main-nav a.active { border-bottom: 1px solid var(--white); }
  .account {
    position: absolute; top: 40px; left: 907px; color: var(--white);
    font-family: "Lato", Arial, sans-serif; font-size: 13px; display: flex; align-items: center; gap: 8px;
  }

  .section-title {
    position: absolute; left: 0; width: 1130px; text-align: center;
    font-family: "Lato", Arial, sans-serif; font-size: 25px; font-weight: 400; text-transform: uppercase;
  }
  .section-title.strong { font-weight: 700; }
  .rule { position: absolute; left: 93px; width: 944px; height: 1px; background: var(--line); }

  .field-label { position: absolute; font-size: 12px; color: var(--muted); }
  .field {
    position: absolute; border: 1px solid var(--field-line); background: var(--white);
    font-size: 12px; color: var(--muted); display: flex; align-items: center; padding: 0 15px;
  }
  .field.select { justify-content: space-between; }
  .field.textarea { align-items: flex-start; padding-top: 14px; }
  .field svg { flex: none; }

  .btn {
    position: absolute; background: var(--accent); color: var(--white); border: none;
    font-family: "Lato", Arial, sans-serif; font-weight: 700; text-transform: uppercase;
    display: flex; align-items: center; justify-content: center;
  }
  .btn-update { left: 471px; top: 498px; width: 187px; height: 47px; border-radius: 6px; font-size: 14px; }

  .note { position: absolute; left: 0; top: 702px; width: 1130px; text-align: center; font-size: 11px; color: var(--muted); }

  .drivers { position: absolute; left: 93px; top: 749px; width: 944px; border-collapse: collapse; }
  .drivers th {
    background: var(--table-head); color: var(--white); height: 53px; text-align: left;
    font-family: "Lato", Arial, sans-serif; font-weight: 700; font-size: 13px;
  }
  .drivers td { height: 65px; font-size: 11.5px; color: var(--ink); border-bottom: 1px solid var(--line); }
  .drivers tr:last-child td { border-bottom: none; }
  .drivers th:first-child, .drivers td:first-child { padding-left: 16px; }
  .col-name { width: 181px; } .col-dist { width: 204px; } .col-time { width: 210px; } .col-status { width: 210px; }
  .status {
    display: inline-block; width: 113px; height: 24px; line-height: 24px; padding-left: 11px;
    color: var(--white); font-family: "Lato", Arial, sans-serif; font-size: 13.5px;
  }
  .status.accepted { background: var(--ok); }
  .status.sent { background: var(--sent); }
  .status.pending { background: var(--pending); }
  .btn-pay { position: static; width: 129px; height: 36px; font-size: 13.5px; font-weight: 400; }

  .site-footer { position: absolute; left: 0; top: 1123px; width: 1130px; border-top: 1px solid var(--line); }
  .copyright { text-align: center; padding-top: 31px; font-size: 11.5px; color: var(--muted); }
</style>
</head>
<body>
  <header class="site-header" role="img" aria-label="Light blue faceted header band">
    <div class="brand"><span class="brand-dot"></span>HAULVEK</div>
    <nav class="main-nav">
      <a href="#">Book</a>
      <a href="#">How it wows</a>
      <a href="#" class="active">Become a driver</a>
    </nav>
    <div class="account">sam@mailvexa.com
      <svg width="9" height="6" viewBox="0 0 9 6"><path d="M1 1l3.5 3.5L8 1" fill="none" stroke="#fff" stroke-width="1.3"/></svg>
    </div>
  </header>

  <main>
    <h1 class="section-title" style="top:198px">Booking details</h1>
    <div class="rule" style="top:254px"></div>

    <label class="field-label" style="left:186px;top:288px">Package selected:</label>
    <div class="field select" style="left:187px;top:312px;width:336px;height:40px">
      Package 1
      <svg width="9" height="6" viewBox="0 0 9 6"><path d="M1 1l3.5 3.5L8 1" fill="none" stroke="#555" stroke-width="1.2"/></svg>
    </div>

    <label class="field-label" style="left:606px;top:288px">Pick-up time selected:</label>
    <div class="field" style="left:607px;top:312px;width:336px;height:40px;gap:12px">
      <svg width="13" height="13" viewBox="0 0 13 13"><rect x="0.5" y="1.5" width="12" height="11" fill="none" stroke="#666"/><path d="M0.5 4.5h12M3 0v3M10 0v3M4.5 4.5v8M8.5 4.5v8M0.5 8.5h12" stroke="#666" fill="none"/></svg>
      July 18 at 0:13 am
    </div>

    <label class="field-label" style="left:186px;top:374px">Description:</label>
    <div class="field textarea" style="left:187px;top:398px;width:756px;height:68px">1 Large Stove</div>

    <button class="btn btn-update">Update your details</button>

    <h2 class="section-title strong" style="top:644px">Drivers in your area</h2>
    <p class="note">Please stay on this Page and be patient,While we contact the drives and find you one ASAP</p>

    <table class="drivers">
      <thead>
        <tr><th class="col-name">NAME</th><th class="col-dist">DISTANCE(KM)</th><th class="col-time">AGREED PICK-UP TIME</th><th class="col-status"></th><th></th></tr>
      </thead>
      <tbody>
        <tr><td>Dorian Pell</td><td>4.04km away</td><td>July 18 at 4.13 am</td><td><span class="status accepted">Time Accepted</span></td><td><button class="btn btn-pay">Make payment</button></td></tr>
        <tr><td>Marcus Tully</td><td>5.7km away</td><td>-</td><td><span class="status sent">Request Sent</span></td><td></td></tr>
        <tr><td>Owen Brask</td><td>11.13km away</td><td>-</td><td><span class="status sent">Request Sent</span></td><td></td></tr>
        <tr><td>Reid Calloway</td><td>11.91km away</td><td>-</td><td><span class="status pending">Pending</span></td><td></td></tr>
      </tbody>
    </table>
  </main>

  <footer class="site-footer">
    <p class="copyright">© Copyright 2017 Haulvek. All Rights Reserved</p>
  </footer>
</body>
</html>
```